Tralha Cesto Website

Tralha Cesto is a brazilian Self Storage in a Box where customers can store all the clutter that they have out of their houses. We deliver one or more boxes at their homes, they fill the boxes with their stuff and we store it for them.

"Tralha" means something like "mess" in portuguese. So the name would means something like "Mess Box" or "Clutter Box".

How it works:
1) The customer asks for 1 or more boxes.
2) Tralha Cesto leaves the boxes at their houses
3) The clients fill the boxes with their stuff
4) Customers call Tralha Cesto for the pick up
5) We get the boxes and store them
6) When the customer wants the box back they can order it online or by phone and wait for the box delivery.
-

We have already produced a flyer to launch the service. You can see this flyer at "Project Files".

We want the website to have a startup "look and fell". Here are some websites of similar services that we like very much.
- www.crateowl.example
- www.stowpod.example

We are planning this launching website to have only 2 pages. The Landing Page and a FAQ page. We are producing an explainer video. The proposed designs must think about a special place to place the video.

We are still writing it´s content but you can use the flyer as a reference.

Thanks.
Updates

Project Deadline Extended
Reason: The project was refundable but as we have already received good design options, now we are turning it to Non Refundable and giving more time for new designers to send their proposals. Thanks.

Project Deadline Extended

Target Market(s)

Young couples having kids
Students
Families in need of more space at home

Industry/Entity Type

Store

Requirements
Must have
• Special place to place the explainer video (still being produced).

How it works drawing. You can use the one on the flyer or draw a new one (recomended).

Transparent box drawings (showing it´s content). I will serve to show the clients what they can store with the service.

Clutter Room Before/After Pic/drawings (showing how the service can benefit the client).

```html
<!DOCTYPE html>
<html lang="en">
<head>
<meta charset="utf-8">
<title>Tralha Cesto — Self Storage in a Box</title>
<link rel="stylesheet" href="https://fonts.googleapis.com/css2?family=Arimo:wght@400;700&family=Open+Sans:wght@400;600;700&family=Oswald:wght@400&display=swap">
<style>
  :root {
    --orange: #f39317;
    --orange-dark: #d97f0c;
    --blue: #1565b5;
    --nav-blue: #1a6ec1;
    --band-blue: #7da8d6;
    --ink: #333333;
    --muted: #666666;
    --line: #cfcfcf;
    --pale: #f3f3f3;
    --bar-black: #1d1d1d;
    --footer: #3c3f42;
    --footer-base: #2d2f31;
    --footer-text: #b9bcbf;
    --white: #ffffff;
  }
  * { box-sizing: border-box; margin: 0; padding: 0; }
  html, body { width: 1200px; height: 2560px; overflow: hidden; }
  body { position: relative; background: var(--white); font-family: "Arimo", Arial, sans-serif; color: var(--ink); }
  .abs { position: absolute; }

  /* header */
  .top-stripe { left: 0; top: 0; width: 1200px; height: 6px; background: var(--orange); }
  .brand { left: 200px; top: 18px; width: 220px; height: 76px; }
  .brand-dot { left: 44px; top: 0; width: 34px; height: 34px; border-radius: 50%; background: var(--orange); }
  .brand-name { left: 0; top: 44px; font-size: 24px; font-weight: 700; color: var(--blue); white-space: nowrap; }
  .account { left: 858px; top: 0; display: flex; gap: 2px; }
  .account a { display: flex; align-items: center; gap: 6px; height: 30px; padding: 0 10px; background: var(--orange); color: var(--white); font-size: 12px; font-weight: 700; text-decoration: none; }
  .account svg { width: 11px; height: 11px; }
  .hotline { left: 832px; top: 48px; display: flex; align-items: center; gap: 10px; color: var(--orange); font-size: 22px; font-weight: 700; }
  .hotline svg { width: 40px; height: 34px; }

  /* nav */
  .nav { left: 0; top: 99px; width: 1200px; height: 44px; background: var(--nav-blue); }
  .nav ul { list-style: none; position: absolute; left: 200px; top: 0; display: flex; height: 44px; }
  .nav li { height: 44px; display: flex; align-items: center; justify-content: center; color: var(--white); font-size: 11px; }
  .nav li.active { background: var(--orange); }
  .social-top { left: 878px; top: 109px; display: flex; gap: 5px; }
  .social-top span { width: 19px; height: 19px; border-radius: 3px; background: #dfe9f5; }

  /* hero */
  .hero { left: 0; top: 143px; width: 1200px; height: 415px; background: linear-gradient(100deg, #4a3a2c 0%, #7b6652 28%, #a59784 50%, #6e5a48 72%, #3e3228 100%); }
  .play { left: 556px; top: 292px; width: 82px; height: 82px; }

  /* promo band */
  .promo { left: 0; top: 558px; width: 1200px; height: 89px; background: var(--blue); }
  .promo-title { left: 273px; top: 16px; color: var(--white); font-size: 24px; font-weight: 700; line-height: 29px; }
  .promo-brace { left: 420px; top: 12px; width: 44px; height: 66px; }
  .promo-text { left: 495px; top: 18px; width: 340px; color: var(--orange); font-size: 18px; line-height: 24px; }
  .btn { display: flex; align-items: center; justify-content: center; background: var(--orange); color: var(--white); font-weight: 700; border-bottom: 3px solid var(--orange-dark); }
  .promo-btn { left: 855px; top: 582px; width: 108px; height: 38px; font-size: 15px; font-weight: 400; border: 1px solid #f7b55a; }

  /* headings */
  .section-title { left: 0; width: 1200px; text-align: center; font-size: 28px; color: var(--blue); }
  .section-title em { font-style: normal; color: var(--orange); }
  .lede { left: 200px; width: 800px; text-align: center; font-size: 10px; line-height: 15px; color: var(--muted); }

  /* how it works */
  .steps { left: 0; top: 840px; width: 1200px; height: 260px; }
  .step-num { font-family: "Oswald", sans-serif; font-size: 17px; fill: #222; }
  .step-icon { fill: var(--nav-blue); }

  /* app band */
  .app-band { left: 0; top: 1111px; width: 1200px; height: 284px; background: var(--band-blue); }
  .app-text { left: 200px; top: 1152px; width: 380px; color: var(--white); font-size: 10px; line-height: 17.5px; }
  .read-more { width: 136px; height: 33px; font-size: 10px; }
  .devices { left: 589px; top: 1130px; width: 410px; height: 244px; border-radius: 8px; background: linear-gradient(135deg, #e8e8e8 0%, #c9342e 35%, #b72c28 60%, #f2f2f2 100%); }

  /* before / after */
  .photo { top: 1418px; width: 380px; height: 253px; }
  .photo-before { left: 200px; background: linear-gradient(135deg, #6c7478 0%, #3b3f42 45%, #8d8a84 100%); }
  .photo-after { left: 620px; background: linear-gradient(135deg, #8b8a7c 0%, #6f6b5c 40%, #a58e67 100%); }
  .photo-label { top: 1688px; width: 380px; text-align: center; font-size: 19px; font-weight: 700; }

  /* sizes */
  .sizes { left: 0; top: 1801px; width: 1200px; height: 282px; background: var(--pale); }
  .box-art { left: 253px; top: 1835px; width: 259px; height: 205px; background: linear-gradient(135deg, #4d5a6b 0%, #9aa4ae 45%, #c9b89a 100%); }
  .sizes-title { left: 550px; top: 1850px; font-size: 14px; line-height: 19px; color: var(--blue); text-transform: uppercase; }
  .sizes-text { left: 550px; top: 1900px; width: 375px; font-size: 10px; line-height: 19px; color: var(--muted); }
  .slider-arrow { top: 1928px; width: 24px; height: 24px; border: 1px solid var(--blue); border-radius: 3px; background: var(--white); }

  /* quote */
  .try-title { left: 198px; top: 2152px; font-size: 25px; font-weight: 700; color: #111; }
  .try-sub { left: 208px; top: 2188px; font-size: 14px; color: #111; }
  .try-arrow { left: 305px; top: 2196px; width: 95px; height: 40px; }
  .quote { left: 400px; top: 2151px; width: 595px; height: 72px; background: var(--white); border: 1px solid #d6d6d6; box-shadow: 0 2px 6px rgba(0,0,0,.15); }
  .quote-field { left: 24px; top: 28px; font-size: 12px; color: #888; }
  .quote-btn { left: 395px; top: 0; width: 200px; height: 72px; background: var(--blue); color: var(--white); font-size: 15px; font-weight: 700; display: flex; align-items: center; justify-content: center; }

  /* support bar */
  .support { left: 0; top: 2250px; width: 1200px; height: 92px; background: var(--bar-black); }
  .support-item { top: 18px; width: 160px; margin-left: -80px; text-align: center; color: var(--white); font-size: 15px; }
  .support-item svg { display: block; margin: 0 auto 8px; width: 24px; height: 22px; }

  /* footer */
  .footer { left: 0; top: 2342px; width: 1200px; height: 171px; background: var(--footer); font-family: "Open Sans", Arial, sans-serif; }
  .foot-col { top: 28px; width: 210px; color: var(--footer-text); font-size: 9.5px; line-height: 15px; }
  .foot-col h4 { color: var(--white); font-size: 11px; font-weight: 700; text-transform: uppercase; margin-bottom: 14px; }
  .contact-row { display: flex; gap: 8px; margin-bottom: 3px; }
  .contact-row svg { flex: none; width: 9px; height: 10px; margin-top: 3px; }
  .contact-row b { color: var(--white); font-weight: 600; }
  .post { padding-bottom: 6px; margin-bottom: 8px; border-bottom: 1px solid #55595d; }
  .post strong { display: block; color: var(--white); font-weight: 600; }
  .news-form { display: flex; gap: 3px; margin-top: 12px; }
  .news-input { width: 128px; height: 20px; background: var(--white); }
  .news-btn { width: 50px; height: 20px; background: var(--nav-blue); color: var(--white); font-size: 9px; font-weight: 700; display: flex; align-items: center; justify-content: center; }
  .follow { display: flex; gap: 5px; }
  .follow span { width: 18px; height: 18px; border-radius: 50%; background: var(--white); }
  .base { left: 0; top: 2513px; width: 1200px; height: 47px; background: var(--footer-base); font-family: "Open Sans", Arial, sans-serif; font-size: 10px; color: var(--footer-text); }
  .base-copy { left: 200px; top: 17px; }
  .base-links { left: 891px; top: 17px; display: flex; gap: 14px; }
</style>
</head>
<body>

<div class="abs top-stripe"></div>

<header>
  <div class="abs brand">
    <span class="abs brand-dot"></span>
    <span class="abs brand-name">Tralha Cesto</span>
  </div>
  <div class="abs account">
    <a href="#"><svg viewBox="0 0 12 12"><rect x="1" y="1" width="10" height="10" fill="none" stroke="#fff" stroke-width="1.4"/><path d="M3 6h5M6 4l2 2-2 2" fill="none" stroke="#fff" stroke-width="1.4"/></svg>Login</a>
    <a href="#"><svg viewBox="0 0 12 12"><rect x="1" y="1" width="10" height="10" fill="none" stroke="#fff" stroke-width="1.4"/><path d="M3 4h6M3 6h6M3 8h4" stroke="#fff" stroke-width="1.2"/></svg>Register</a>
  </div>
  <div class="abs hotline">
    <svg viewBox="0 0 40 34"><path d="M4 14c0-7 32-7 32 0l-2 4-7-2v-3c-4-1-10-1-14 0v3l-7 2z" fill="#1565b5"/><path d="M10 18h20l4 13H6z" fill="#1565b5"/><circle cx="20" cy="25" r="4" fill="#fff"/></svg>
    (11) 4020 7718
  </div>
</header>

<nav class="abs nav">
  <ul>
    <li class="active" style="width:97px">Home</li>
    <li style="width:135px">Who We Are</li>
    <li style="width:130px">What We Do</li>
    <li style="width:130px">Testimonials</li>
    <li style="width:120px">Contact us</li>
  </ul>
</nav>
<div class="abs social-top"><span></span><span></span><span></span><span></span><span></span></div>

<section>
  <div class="abs hero" role="img" aria-label="Photo of a storage room with wooden shelves full of cardboard boxes, where the explainer video plays"></div>
  <svg class="abs play" viewBox="0 0 82 82"><circle cx="41" cy="41" r="38" fill="#4a8fe0" stroke="#cfe2f8" stroke-width="5"/><circle cx="41" cy="41" r="27" fill="#fff"/><path d="M34 27l20 14-20 14z" fill="#3a7fd6"/></svg>
</section>

<section class="abs promo">
  <div class="abs promo-title">Brand<br>Running</div>
  <svg class="abs promo-brace" viewBox="0 0 44 66"><path d="M4 3c14 0 14 12 14 22 0 6 4 8 20 8-16 0-20 2-20 8 0 10 0 22-14 22" fill="none" stroke="#f39317" stroke-width="4"/></svg>
  <div class="abs promo-text">Fast delivery and safe storage. More space at home from day one</div>
</section>
<div class="abs btn promo-btn">Click here</div>

<section>
  <h1 class="abs section-title" style="top:668px;font-weight:400">Welcome Tralha <em>Cesto</em></h1>
  <p class="abs lede" style="top:713px">We drop sturdy boxes at your door, you fill them with the things you rarely use, and we carry them to our safe storage. When you miss something, order it back online or by phone and we bring the box home to you. No trucks to rent, no keys to lose, just more space.</p>
</section>

<section>
  <h2 class="abs section-title" style="top:780px;font-weight:400">How It <em>Works</em></h2>
  <svg class="abs steps" viewBox="0 840 1200 260" aria-label="Four steps from box delivery to storage">
    <g fill="none" stroke="#cfcfcf" stroke-width="1.4">
      <path d="M230 1011 Q262 972 284 960"/>
      <path d="M356 930 Q440 900 494 904"/>
      <path d="M582 940 Q640 1000 644 1006"/>
      <path d="M746 1006 Q800 960 838 944"/>
      <path d="M938 912 Q960 904 976 900"/>
    </g>
    <circle cx="230" cy="1011" r="6" fill="#fff" stroke="#8fc7b8" stroke-width="1.5"/>
    <circle cx="976" cy="900" r="7" fill="#fff" stroke="#8fc7b8" stroke-width="1.5"/>
    <g fill="#fff" stroke="#cfcfcf" stroke-width="1.4">
      <circle cx="321" cy="944" r="51"/>
      <circle cx="545" cy="906" r="51"/>
      <circle cx="695" cy="1012" r="51"/>
      <circle cx="888" cy="930" r="51"/>
    </g>

    <!-- step 1: house and a box at the door -->
    <g class="step-icon" transform="translate(321 944)">
      <path d="M-28 -2 L-14 -16 L0 -2 L-4 -2 L-4 14 L-24 14 L-24 -2 Z"/>
      <rect x="-17" y="4" width="6" height="10" fill="#fff"/>
      <rect x="4" y="-2" width="22" height="16"/>
      <path d="M4 3 H26" stroke="#fff" stroke-width="1.5"/>
      <rect x="13" y="-2" width="4" height="6" fill="#fff"/>
    </g>

    <!-- step 2: open box with things inside -->
    <g class="step-icon" transform="translate(545 906)">
      <rect x="-12" y="-24" width="8" height="10"/>
      <circle cx="6" cy="-20" r="5"/>
      <rect x="10" y="-28" width="3" height="14"/>
      <path d="M-18 -12 H18 V18 H-18 Z"/>
      <path d="M-18 -12 L-26 -4 L-18 -4 Z"/>
      <path d="M18 -12 L26 -4 L18 -4 Z"/>
      <rect x="-5" y="-6" width="10" height="7" fill="#fff"/>
    </g>

    <!-- step 3: truck driving to a house -->
    <g class="step-icon" transform="translate(695 1012)">
      <rect x="-30" y="-6" width="26" height="18"/>
      <path d="M-3 0 H6 L11 6 V12 H-3 Z"/>
      <circle cx="-22" cy="14" r="4" stroke="#fff" stroke-width="1.5"/>
      <circle cx="4" cy="14" r="4" stroke="#fff" stroke-width="1.5"/>
      <path d="M12 -10 L22 -20 L32 -10 L29 -10 L29 4 L15 4 L15 -10 Z"/>
      <rect x="20" y="-5" width="4" height="9" fill="#fff"/>
    </g>

    <!-- step 4: phone ordering a box back home -->
    <g class="step-icon" transform="translate(888 930)">
      <path d="M-30 -2 L-16 -16 L-2 -2 L-5 -2 L-5 14 L-27 14 L-27 -2 Z"/>
      <rect x="-20" y="2" width="10" height="8" fill="#fff"/>
      <rect x="4" y="-18" width="16" height="30" rx="3"/>
      <rect x="7" y="-13" width="10" height="18" fill="#fff"/>
      <path d="M24 -12 Q28 -6 24 0 M27 -15 Q33 -6 27 3" fill="none" stroke="#1a6ec1" stroke-width="1.6"/>
    </g>

    <g fill="none" stroke="#333" stroke-width="1.3">
      <path d="M316 1036 Q292 1030 284 1016"/><path d="M280 1022 l4-7 5 5"/>
      <path d="M455 862 Q472 848 490 850"/><path d="M484 845 l7 5-6 5"/>
      <path d="M598 1010 Q616 1030 640 1032"/><path d="M634 1027 l7 5-7 4"/>
      <path d="M880 1062 Q902 1056 912 1030"/><path d="M906 1034 l6-5 3 8"/>
    </g>
    <text class="step-num" x="322" y="1056">01</text>
    <text class="step-num" x="425" y="871">02</text>
    <text class="step-num" x="568" y="1029">03</text>
    <text class="step-num" x="850" y="1073">04</text>
  </svg>
</section>

<section>
  <div class="abs app-band"></div>
  <p class="abs app-text">Manage every box from your phone or laptop. See a list of what you stored, add photos and notes, and ask for a delivery in a few taps. Our team confirms the time, brings the box to your door and takes back the ones you no longer need at home. You pay only for the boxes you keep with us each month, with no long contract and no hidden fees. Students, young families and anyone short on room can start with one box today.</p>
  <div class="abs btn read-more" style="left:200px;top:1321px">Read More +</div>
  <div class="abs devices" role="img" aria-label="Laptop and smartphone showing the online shop and box manager screens"></div>
</section>

<section>
  <div class="abs photo photo-before" role="img" aria-label="Photo of a cluttered home office before the service"></div>
  <div class="abs photo photo-after" role="img" aria-label="Photo of the same office tidy after the service"></div>
  <div class="abs photo-label" style="left:200px;color:var(--blue)">Before</div>
  <div class="abs photo-label" style="left:620px;color:var(--orange)">After</div>
  <p class="abs lede" style="top:1736px">Clear the floor, free the shelves and get your room back. Seasonal clothes, toys, books and sports gear wait safely with us until you need them again.</p>
</section>

<section>
  <div class="abs sizes"></div>
  <div class="abs box-art" role="img" aria-label="Drawing of a transparent box showing folded clothes, shoes, books and a dartboard inside"></div>
  <h3 class="abs sizes-title" style="font-weight:400">Pick the size that meets your<br>storage needs.</h3>
  <p class="abs sizes-text">Our boxes come in three sizes, from a small case for documents to a large crate for bedding and winter coats. Each box is sealed, labelled and kept in a dry, watched room. Tell us what you plan to store and we suggest the right boxes.</p>
  <div class="abs btn read-more" style="left:550px;top:2011px;width:140px">Read More +</div>
  <svg class="abs slider-arrow" style="left:201px" viewBox="0 0 24 24"><path d="M14 7l-5 5 5 5" fill="none" stroke="#1565b5" stroke-width="2"/></svg>
  <svg class="abs slider-arrow" style="left:973px" viewBox="0 0 24 24"><path d="M10 7l5 5-5 5" fill="none" stroke="#1565b5" stroke-width="2"/></svg>
</section>

<section>
  <div class="abs try-title">Try us now!</div>
  <div class="abs try-sub">Get a free quote!</div>
  <svg class="abs try-arrow" viewBox="0 0 95 40"><path d="M4 30 Q50 36 88 22" fill="none" stroke="#333" stroke-width="1.3"/><path d="M80 19l8 3-6 6" fill="none" stroke="#333" stroke-width="1.3"/></svg>
  <div class="abs quote">
    <span class="abs quote-field">What are you looking for?</span>
    <span class="abs quote-btn">Get quote now</span>
  </div>
</section>

<section class="abs support">
  <div class="abs support-item" style="left:234px">
    <svg viewBox="0 0 24 22"><path d="M5 2l4 1 1 5-3 2c1 3 3 5 6 6l2-3 5 1 1 4c-1 2-3 3-5 3C9 20 3 13 3 6c0-2 1-3 2-4z" fill="#fff"/></svg>Talk to u
  </div>
  <div class="abs support-item" style="left:464px">
    <svg viewBox="0 0 24 22"><ellipse cx="12" cy="9" rx="11" ry="8" fill="#fff"/><path d="M6 14l-2 7 7-5z" fill="#fff"/></svg>Live Chat
  </div>
  <div class="abs support-item" style="left:700px">
    <svg viewBox="0 0 24 22"><rect x="1" y="3" width="22" height="16" rx="1" fill="#fff"/><path d="M1 4l11 8 11-8" fill="none" stroke="#1d1d1d" stroke-width="2"/></svg>Email Us
  </div>
  <div class="abs support-item" style="left:935px">
    <svg viewBox="0 0 24 22"><rect x="1" y="9" width="5" height="12" fill="#fff"/><path d="M8 9l5-8c2 0 3 1 3 3l-1 4h6c1 0 2 1 2 2l-2 9c0 1-1 2-2 2H8z" fill="#fff"/></svg>Good Support
  </div>
</section>

<footer>
  <div class="abs footer">
    <div class="abs foot-col" style="left:200px">
      <h4>Contact Info</h4>
      <div class="contact-row"><svg viewBox="0 0 9 10"><path d="M4.5 0a3 3 0 0 1 3 3c0 2-3 7-3 7S1.5 5 1.5 3a3 3 0 0 1 3-3z" fill="#8a8e92"/></svg><span><b>Address:</b> 214 Rua das Caixas, 01310 São Paulo, Brasil</span></div>
      <div class="contact-row"><svg viewBox="0 0 9 10"><rect x="2" y="0" width="5" height="10" rx="1" fill="#8a8e92"/></svg><span><b>Telephones:</b> +55 11 4020-7718</span></div>
      <div class="contact-row"><svg viewBox="0 0 9 10"><rect x="0" y="2" width="9" height="6" fill="#8a8e92"/></svg><span><b>E-mail:</b> ola@tralhacesto.example</span></div>
    </div>
    <div class="abs foot-col" style="left:423px">
      <h4>Recent Posts</h4>
      <div class="post"><strong>This is a Standard Post</strong>November 21, 2013</div>
      <div class="post"><strong>This is a Gallery Post</strong>October 20, 2013</div>
    </div>
    <div class="abs foot-col" style="left:649px">
      <h4>Newsletter</h4>
      <p>Subscribe and stay up to date with the latest news from us.</p>
      <div class="news-form"><span class="news-input"></span><span class="news-btn">SUBMIT</span></div>
    </div>
    <div class="abs foot-col" style="left:872px">
      <h4>Follow Us</h4>
      <div class="follow"><span></span><span></span><span></span><span></span><span></span><span></span></div>
    </div>
  </div>
  <div class="abs base">
    <span class="abs base-copy">Content copyright 2014. Tralha Cesto. All rights reserved.</span>
    <span class="abs base-links"><span>FAQ's</span><span>About</span><span>Contact</span></span>
  </div>
</footer>

</body>
</html>
```